BrimFalcon Business Cards

We have a defined brand. Please visit our website to get a feel for the product and the color pallets. www.brimfalcon-example.com

We need an updated, world class business card design. (See the attached existing card design). Please utilize BOTH sides of the card as shown and be creative with the layout. I do want the horse head icon to be positioned as it is with the existing card.

The remainder of the layout can be customized and I also want it vertically oriented.

Attached are the logo files and please use the colors as follows:
Green - #A5CE39
Tan - #CDBD99
Black

Feel free to play with the colors.

```html
<!DOCTYPE html>
<html lang="en">
<head>
<meta charset="utf-8">
<title>BrimFalcon Business Card</title>
<link href="https://fonts.googleapis.com/css2?family=Montserrat:wght@400;500;600&display=swap" rel="stylesheet">
<style>
  :root {
    --page-bg: #1c1c1c;
    --card-black: #151515;
    --ink-white: #f4f4f4;
    --brand-green: #a5ce39;
    --deep-green: #3f9a3c;
    --mark-grey: #2a2a2a;
  }
  * { margin: 0; padding: 0; box-sizing: border-box; }
  html, body { width: 1200px; height: 900px; overflow: hidden; }
  body {
    background: var(--page-bg);
    font-family: "Montserrat", sans-serif;
    display: flex;
    align-items: center;
    justify-content: center;
    gap: 80px;
  }
  .card {
    position: relative;
    width: 360px;
    height: 630px;
    background: var(--card-black);
    box-shadow: 0 14px 40px rgba(0,0,0,.55);
    overflow: hidden;
  }
  .card__edge {
    position: absolute;
    left: 0; right: 0; bottom: 0;
    height: 7px;
    background: linear-gradient(90deg, var(--brand-green), var(--deep-green));
  }
  /* front */
  .brand {
    position: absolute;
    left: 40px;
    right: 40px;
    top: 130px;
    color: var(--ink-white);
  }
  .brand__name {
    display: flex;
    align-items: center;
    gap: 12px;
    font-weight: 600;
    font-size: 32px;
    letter-spacing: .5px;
    white-space: nowrap;
  }
  .brand__dot {
    width: 30px; height: 30px;
    border-radius: 50%;
    background: var(--ink-white);
    flex: none;
  }
  .brand__tagline {
    margin-top: 8px;
    margin-left: 42px;
    font-size: 11px;
    letter-spacing: 3px;
    white-space: nowrap;
  }
  .divider {
    position: absolute;
    left: 40px;
    top: 262px;
    width: 220px;
    height: 1.5px;
    background: var(--deep-green);
  }
  .contact {
    position: absolute;
    left: 40px;
    right: 30px;
    top: 292px;
    color: var(--ink-white);
    font-size: 15px;
    line-height: 1.5;
  }
  .contact__name {
    color: var(--brand-green);
    font-weight: 600;
    font-size: 22px;
    letter-spacing: .5px;
    text-transform: uppercase;
    line-height: 1.3;
  }
  .contact__place { margin-bottom: 10px; }
  .contact__row { display: flex; align-items: center; gap: 8px; white-space: nowrap; }
  .contact__icon { width: 13px; height: 13px; flex: none; }
  /* back */
  .back-mark {
    position: absolute;
    left: 50%;
    top: 40%;
    transform: translate(-50%, -50%);
    color: var(--mark-grey);
    font-weight: 600;
    font-size: 34px;
    display: flex;
    align-items: center;
    gap: 12px;
    white-space: nowrap;
  }
  .back-mark__dot {
    width: 32px; height: 32px;
    border-radius: 50%;
    background: var(--mark-grey);
    flex: none;
  }
</style>
</head>
<body>
  <section class="card card--front">
    <div class="brand">
      <div class="brand__name"><span class="brand__dot"></span>BrimFalcon</div>
      <div class="brand__tagline">Performance Driven EVs</div>
    </div>
    <div class="divider"></div>
    <div class="contact">
      <div class="contact__name">Dana Ketter</div>
      <div>President &amp; CEO</div>
      <div class="contact__place">Harlow Bay, Northland<br>Canada</div>
      <div class="contact__row">
        <svg class="contact__icon" viewBox="0 0 16 16"><path fill="#a5ce39" d="M4 1l3 3-2 2c1 2 3 4 5 5l2-2 3 3-2 3C7 15 1 9 1 3z"/></svg>
        555.014.2290
      </div>
      <div class="contact__row">
        <svg class="contact__icon" viewBox="0 0 16 16"><rect x="1" y="3" width="14" height="10" fill="#a5ce39"/><path d="M1 3l7 6 7-6" fill="none" stroke="#151515" stroke-width="1.5"/></svg>
        dana@brimfalcon-example.com
      </div>
      <div class="contact__row">
        <svg class="contact__icon" viewBox="0 0 16 16"><circle cx="8" cy="8" r="7" fill="#a5ce39"/><path d="M1 8h14M8 1c-3 4-3 10 0 14M8 1c3 4 3 10 0 14" fill="none" stroke="#151515" stroke-width="1"/></svg>
        brimfalcon-example.com
      </div>
    </div>
    <div class="card__edge"></div>
  </section>

  <section class="card card--back">
    <div class="back-mark"><span class="back-mark__dot"></span>BrimFalcon</div>
    <div class="card__edge"></div>
  </section>
</body>
</html>
```